Brightmoor - a website to encourage people to spend time in nature

I have a squarespace site with some content on it but the squarespace template doesn't completely suit my needs, I keep fiddling with the template but actually I need some professional help to get it looking the way I want and with the right 'mood'.
The website is for "Brightmoor" - it will be a blog where I write about the importance of nature for good health. I also want to use the website to market services such as outdoor coaching, retreats and walking workshops.
This has been in my head for a LONG time and I currently only use instagram for micro-blogs but it's time for me to get this moving. I've previously engaged other designers on branding for it but they just didn't get it quite the way that I wanted it and I wasn't completely happy with the results. It's been a process for me as to what I want but in the meantime I just didn't come back to the design aspect of it now. I'm looking for a designer who understands the purpose of the website, the ethos and can help me realise this into a design that's clean, clear and simple.

Please note that I have a domain (brightmoor.org) and a lot of content drafted on squarespace already. I have published it with password protection - password is brightmoor2020 - it still has some of the original template on it, but does have some content. Don't take it as anything to follow in particular, i am looking for fresh eyes and fresh ideas.

Target Market(s)

There are three main groups that I want to target - people who are suffering from stress and anxiety, people who treat them and parents who want to get their kids outside (thereby preventing stress and anxiety)

Contact Information for Business Card

Joan Petrie
Brightmoor
Telephone +44 7700 900417
brightmoor@mailvane.com

Logo Text

Brightmoor - if that. I have an idea that the logo should have a leaf on it somewhere, or maybe just be a leaf.

Coding

Coded - Design and coding required

Number of Pages Required

5+ page

Font styles to use
Serif
Sans Serif

Colors
add136
33b8a4
34a6d7
3377b5

Requirements
Must have
• Space for lots of images. The ability for me to edit the pages if I need to. Be user friendly. Look beautiful.
• For an idea of the images I use and the content I'm interested in writing about have a look at @brightmoor on instagram.
• That pop up about cookies so I am complying with data laws.
Should not have
• Must not be too 'busy' I'd like to avoid too much movement.

```html
<!DOCTYPE html>
<html lang="en">
<head>
<meta charset="utf-8">
<title>Brightmoor – Services pages</title>
<link href="https://fonts.googleapis.com/css2?family=Lora:ital,wght@0,400;0,600;0,700;1,600;1,700&family=Poppins:wght@400;500&display=swap" rel="stylesheet">
<style>
  :root{
    --paper:#ffffff;
    --label:#2aa38f;
    --leaf:#3dbd6e;
    --leaf-bright:#45c777;
    --logo:#4fd0a4;
    --nav-text:#f6ece6;
    --nav-frame:#8fdccd;
    --card:rgba(58,176,156,0.58);
    --card-lite:rgba(90,196,176,0.55);
    --card-text:#f3faf7;
    --footer:#0e1f1c;
    --footer-head:#ffffff;
    --footer-link:#3fc381;
    --field:#ffffff;
  }
  *{box-sizing:border-box;margin:0;padding:0}
  html,body{width:1200px;height:1200px;overflow:hidden;background:var(--paper)}
  .board{position:absolute;left:0;top:0;width:1920px;height:1920px;transform:scale(.625);transform-origin:0 0;background:var(--paper)}
  .page-label{position:absolute;font-family:"Lora",serif;font-style:italic;font-weight:600;font-size:30px;color:var(--label)}
  .screen{position:absolute;width:736px;overflow:hidden;background:var(--footer)}
  .hero{position:absolute;left:0;top:0;width:736px}
  .sunset{position:absolute;inset:0;
    background:
      radial-gradient(ellipse 60% 18% at 50% 49%, rgba(255,200,90,.85), rgba(255,200,90,0) 70%),
      linear-gradient(180deg,#7d8593 0%,#b8868a 10%,#de8d6c 22%,#ef9352 36%,#f6a648 46%,#6a5a5c 50%,#54505a 53%,#c7683d 60%,#e58a45 72%,#d9703a 86%,#a9522e 100%)}
  .brand{position:absolute;left:198px;top:22px;font-family:"Lora",serif;font-weight:400;font-size:22px;color:var(--logo);letter-spacing:.2px}
  .nav{position:absolute;top:24px;left:330px;height:17px;display:flex;align-items:center;font-family:"Lora",serif;font-size:9.5px;color:var(--nav-text)}
  .nav span{padding:0 8px}
  .nav .active{border:1px solid var(--nav-frame);border-radius:2px;padding:3px 8px;margin:0 2px}
  .crumb{position:absolute;left:199px;top:78px;font-family:"Lora",serif;font-style:italic;font-weight:700;font-size:27px;color:var(--leaf-bright);text-shadow:0 1px 2px rgba(20,60,40,.35);white-space:nowrap}
  .crumb .sep{color:#fff;font-style:normal;font-weight:400;font-size:20px;padding:0 4px;text-shadow:none}
  .card{position:absolute;left:186px;top:112px;width:364px;background:var(--card);border-radius:3px;padding:12px 12px 0;overflow:hidden}
  .card p{font-family:"Poppins",sans-serif;font-size:6.5px;line-height:11px;color:var(--card-text);margin-bottom:11px}
  .slider{position:absolute;left:0;bottom:0;width:364px;height:115px;background:var(--card-lite)}
  .slide-photo{position:absolute;left:124px;top:18px;width:116px;height:65px;background:linear-gradient(180deg,#4f8fd6 0%,#9cc4ea 40%,#eef2f0 55%,#4c7a34 75%,#3b6a2a 100%)}
  .arrow{position:absolute;top:50px;width:10px;height:14px}
  .dots{position:absolute;left:0;right:0;top:102px;display:flex;justify-content:center;gap:3.5px}
  .dots i{width:4.5px;height:4.5px;border-radius:50%;background:rgba(255,255,255,.5)}
  .dots i:first-child{background:#fff}
  .btn{position:absolute;left:468px;width:82px;height:15px;border-radius:8px;background:var(--leaf);font-family:"Lora",serif;font-size:8.5px;color:#fff;display:flex;align-items:center;justify-content:center}
  .footer{position:absolute;left:0;width:736px;height:155px;background:var(--footer)}
  .foot-brand{position:absolute;left:216px;top:25px;font-family:"Lora",serif;font-size:12px;color:var(--logo)}
  .foot-head{position:absolute;font-family:"Lora",serif;font-weight:700;font-size:7.5px;color:var(--footer-head)}
  .foot-links{position:absolute;left:316px;top:47px;list-style:none}
  .foot-links li{font-family:"Poppins",sans-serif;font-size:6px;line-height:12.8px;color:var(--footer-link)}
  .social-box{position:absolute;left:447px;top:44px;width:11px;height:11px;border:1.3px solid var(--footer-link);border-radius:3px}
  .email{position:absolute;left:433px;top:81px;width:116px;height:14px;background:var(--field);font-family:"Poppins",sans-serif;font-size:5px;color:#8fb0a6;padding:4px 5px}
  .submit{position:absolute;left:433px;top:100px;width:31px;height:12px;border-radius:6px;background:var(--leaf);font-family:"Poppins",sans-serif;font-size:5px;color:#fff;display:flex;align-items:center;justify-content:center}
</style>
</head>
<body>
<div class="board">

  <!-- Retreat -->
  <h2 class="page-label" style="left:102px;top:46px">Services (Retreat)</h2>
  <section class="screen" style="left:102px;top:101px;height:669px">
    <div class="hero" style="height:514px">
      <div class="sunset" role="img" aria-label="Photograph of a sunset over the sea with waves on a beach"></div>
      <div class="brand">Brightmoor</div>
      <nav class="nav"><span>Home</span><span>Origin Story</span><span class="active">Services</span><span>Partners</span><span>Blog</span><span>Contact</span></nav>
      <h1 class="crumb">Services<span class="sep">&gt;</span>Retreat</h1>
      <div class="card" style="height:328px">
        <p>Brightmoor HQ is the very beautiful Hollin Cottage, located at the foot of the Carran Hills in Northern Ireland. 200 years old, steeped in history and in the most breathtaking setting, Hollin Cottage is a stunning retreat venue where you can get away from it all and immerse yourself in the beauty of the Carran countryside. Just a couple of minutes walk away from Ashvale Forest Park, you will be hard pressed to find a better location to reconnect with nature and find yourself.</p>
        <p>Hollin Cottage can be hired by facilitators who wish to take the space and create their own retreat experience. Alternatively, we can create a retreat programme for groups and organisations depending on what you want to achieve in your escape from the ordinary. All retreats are individually programmed to respond to your needs. Together with experienced practitioners, we can offer activities such as meditation, pilates, cold water swimming, forest bathing, nature walks, hikes, foraging and wildlife spotting.</p>
        <p>We look after our guest with the greatest of care. Meals are freshly prepared with the emphasis is on fresh seasonal ingredients, lovingly prepared.</p>
        <p>Everyone can benefit from spending time in nature. Hollin Cottage allows you to get closer to nature whilst enjoying a touch of luxury.</p>
        <div class="slider">
          <svg class="arrow" style="left:10px" viewBox="0 0 10 14"><polyline points="8,1 2,7 8,13" fill="none" stroke="#fff" stroke-width="1.5"/></svg>
          <div class="slide-photo" role="img" aria-label="Photograph of a white cottage with trees and lawn"></div>
          <svg class="arrow" style="right:10px" viewBox="0 0 10 14"><polyline points="2,1 8,7 2,13" fill="none" stroke="#fff" stroke-width="1.5"/></svg>
          <div class="dots"><i></i><i></i><i></i><i></i><i></i><i></i><i></i><i></i><i></i><i></i><i></i><i></i><i></i><i></i><i></i><i></i></div>
        </div>
      </div>
      <div class="btn" style="top:446px">Back to Services</div>
      <div class="btn" style="top:471px">Hire Us</div>
    </div>
    <footer class="footer" style="top:514px">
      <div class="foot-brand">Brightmoor</div>
      <div class="foot-head" style="left:310px;top:30px">Navigation</div>
      <ul class="foot-links"><li>Home</li><li>Origin Story</li><li>Services</li><li>Partners</li><li>Blog</li><li>Contact</li></ul>
      <div class="foot-head" style="left:433px;top:30px">Social Media</div>
      <div class="social-box"></div>
      <div class="foot-head" style="left:433px;top:67px">Subscribe to our newsletter</div>
      <div class="email">Enter your email adress</div>
      <div class="submit">Submit</div>
    </footer>
  </section>

  <!-- Coaching -->
  <h2 class="page-label" style="left:1008px;top:46px">Services (Coaching)</h2>
  <section class="screen" style="left:1008px;top:101px;height:442px">
    <div class="hero" style="height:287px">
      <div class="sunset" role="img" aria-label="Photograph of a sunset over the sea with waves on a beach"></div>
      <div class="brand">Brightmoor</div>
      <nav class="nav"><span>Home</span><span>Origin Story</span><span class="active">Services</span><span>Partners</span><span>Blog</span><span>Contact</span></nav>
      <h1 class="crumb">Services<span class="sep">&gt;</span>Coaching</h1>
      <div class="card" style="height:124px">
        <p>Founder of Brightmoor Joan Petrie is a trained coach who uses natural settings as a tool in her coaching arsenal.</p>
        <p>Only one thing better than coaching and that's coaching in the great outdoors.</p>
        <p>We believe that being out in nature gives you a greater sense of perspective when working through issues and figuring out life's path.</p>
        <p>We are part of nature, not apart from it.</p>
      </div>
      <div class="btn" style="top:243px">Hire Us</div>
    </div>
    <footer class="footer" style="top:287px">
      <div class="foot-brand">Brightmoor</div>
      <div class="foot-head" style="left:310px;top:30px">Navigation</div>
      <ul class="foot-links"><li>Home</li><li>Origin Story</li><li>Services</li><li>Partners</li><li>Blog</li><li>Contact</li></ul>
      <div class="foot-head" style="left:433px;top:30px">Social Media</div>
      <div class="social-box"></div>
      <div class="foot-head" style="left:433px;top:67px">Subscribe to our newsletter</div>
      <div class="email">Enter your email adress</div>
      <div class="submit">Submit</div>
    </footer>
  </section>

  <!-- Consultancy -->
  <h2 class="page-label" style="left:102px;top:876px">Services (Consultancy)</h2>
  <section class="screen" style="left:102px;top:931px;height:586px">
    <div class="hero" style="height:431px">
      <div class="sunset" role="img" aria-label="Photograph of a sunset over the sea with waves on a beach"></div>
      <div class="brand">Brightmoor</div>
      <nav class="nav"><span>Home</span><span>Origin Story</span><span class="active">Services</span><span>Partners</span><span>Blog</span><span>Contact</span></nav>
      <h1 class="crumb">Services<span class="sep">&gt;</span>Consultancy</h1>
      <div class="card" style="height:244px">
        <p>Yes, it's the 'c' word. Consultancy. Blaurgh. Ok, so it raises the hackles and makes you think of corporate bods bestowing theoretical wisdom for the benefit of lesser mortals but this is altogether a more benign affair.</p>
        <p>After a long and varied corporate career, I finally realised the importance of balance and the impact creating balance has on performance. And by balance, I mean time outdoors. I don't mean fitting in a hike on a weekend, I mean time outdoors every day. And I found it was entirely possible to achieve even in a corporate setting. Experimenting with walking meetings, lunchtime skytime and essential movement breaks, I found that my team was happier and less stressed – leading of course to better performance, fewer days off and less presenteeism.</p>
        <p>We offer practical help and advice on how teams can build in the outdoors to their working week without too much hassle or fuss. We can also help you measure the impact on happiness and wellbeing within your organisation.</p>
        <p>We also offer advice to families, schools and other organisations about how to incorporate outdoor time into the everyday and on specific activities that can help build a deeper connection with the natural world. In the busy-ness of modern day life, it can feel overwhelming to have one more thing that has to get done – we have some practical ideas and substitutions that will make getting your nature fix as familiar a habit as brushing your teeth.</p>
      </div>
      <div class="btn" style="top:363px">Back to Services</div>
      <div class="btn" style="top:388px">Hire Us</div>
    </div>
    <footer class="footer" style="top:431px">
      <div class="foot-brand">Brightmoor</div>
      <div class="foot-head" style="left:310px;top:30px">Navigation</div>
      <ul class="foot-links"><li>Home</li><li>Origin Story</li><li>Services</li><li>Partners</li><li>Blog</li><li>Contact</li></ul>
      <div class="foot-head" style="left:433px;top:30px">Social Media</div>
      <div class="social-box"></div>
      <div class="foot-head" style="left:433px;top:67px">Subscribe to our newsletter</div>
      <div class="email">Enter your email adress</div>
      <div class="submit">Submit</div>
    </footer>
  </section>

  <!-- Walks -->
  <h2 class="page-label" style="left:1008px;top:876px">Services (Brightmoor Walks)</h2>
  <section class="screen" style="left:1008px;top:931px;height:804px">
    <div class="hero" style="height:650px">
      <div class="sunset" role="img" aria-label="Photograph of a sunset over the sea with waves on a beach"></div>
      <div class="brand">Brightmoor</div>
      <nav class="nav"><span>Home</span><span>Origin Story</span><span class="active">Services</span><span>Partners</span><span>Blog</span><span>Contact</span></nav>
      <h1 class="crumb">Services<span class="sep">&gt;</span>Brightmoor Walks</h1>
      <div class="card" style="height:462px">
        <p>Brightmoor walks is a walking initiative that aims to get people together in nature on a regular basis. The idea is simple. Get outside, do some moderate exercise with some other folks. Try and do it as often as you can.</p>
        <p>Brightmoor Walking is an initiative aimed at getting people back into nature in the most gentlest of ways – by taking a walk with friends in the great outdoors. The concept is simple – schedule a walk outside, once a week with two or three other people. That's it. Sometimes the best things are the simplest and here's why this works.</p>
        <p>Walking – for most people it's the most accessible form of exercise. You don't need fancy equipment, there are few barriers to entry, it's low impact, it can slot into your day without a huge amount of effort. Its benefits are numerous. [List benefits]</p>
        <p>Outside – research has shown that exercise outdoors is beneficial for your physical and mental health. Spending time in nature has been proven to help reduce stress levels. [more information needed re stress level]</p>
        <p>Weekly commitment – Habit forming. Regular exercise is health promoting. Better to walk for 1 hour once a week than 8 hours once a year. With others – A couple of reasons for this.</p>
        <p>The first is the connection point. Humans need human connection. By regularly scheduling a walking date with others, you are satisfying that need.</p>
        <p>The second is accountability – you are more likely to stick to a commitment if there are other people committing to it as well. Call it peer pressure, call it guilt, whatever. You're more likely to stick to it if you are making a commitment with others.</p>
        <p>This is a programme that we believe works well in a number of settings – particularly GP surgeries, colleges and workplaces. Its main aims are to build meaningful connections between participants and improve wellbeing through time outdoors.</p>
        <p>How it works?</p>
        <p>We will come in, sit down and have a chat about how you think this programme can help your organisation. We take some baseline measurements. We will work out a 'get the message' out there strategy with you and we'll help you market this internally. We will then facilitate the early groups and keep in touch as it progresses. We will do some monitoring to show the impact the scheme is having. We can also tailor the programme specifically with themes or talking points.</p>
        <p>Sometimes it's the simple things that work the best.</p>
      </div>
      <div class="btn" style="top:582px">Back to Services</div>
      <div class="btn" style="top:607px">Hire Us</div>
    </div>
    <footer class="footer" style="top:650px">
      <div class="foot-brand">Brightmoor</div>
      <div class="foot-head" style="left:310px;top:30px">Navigation</div>
      <ul class="foot-links"><li>Home</li><li>Origin Story</li><li>Services</li><li>Partners</li><li>Blog</li><li>Contact</li></ul>
      <div class="foot-head" style="left:433px;top:30px">Social Media</div>
      <div class="social-box"></div>
      <div class="foot-head" style="left:433px;top:67px">Subscribe to our newsletter</div>
      <div class="email">Enter your email adress</div>
      <div class="submit">Submit</div>
    </footer>
  </section>

</div>
</body>
</html>
```